Business Card Design for Varomir Facility Services

We are looking for a Business Card Design for the Company "Varomir Facility Services."
Front side:
- Company Logo (small)
- Company Name, address, pohone, website and personal data.
- white background, for text e.g. company colors (blue or green like in the logo)
Please use following data:
Company data:
Varomir Facility Services Kostelac
Birkenhaldweg 14
6330 Cham
www.varomir-fs.ch
Person data:
Tarik Kostelac
Geschäftsführer
+41 76 519 47 83
info@varomir-fs.ch
Back side:
could be colored in blue or green
please use a big logo sing and some smaller icons to say what is all beeing offered in facility services, like cleaning, maintenance cleaning
industrial cleaning, caretaking, gardening, disposal. There is no need for everyone of the icons if there are similar or an icon is standing for more of them.
colors to use:
blue: HEX 246BB0
green: HEX 52B33E

```html
<!DOCTYPE html>
<html lang="de">
<head>
<meta charset="utf-8">
<title>Varomir Facility Services – Visitenkarte</title>
<link href="https://fonts.googleapis.com/css2?family=Lato:wght@400;700&display=swap" rel="stylesheet">
<style>
  :root {
    --brand-blue: #246BB0;
    --brand-green: #52B33E;
    --text-grey: #5a5a5a;
    --card-white: #ffffff;
    --page-bg: #e9e7e4;
  }
  * { margin: 0; padding: 0; box-sizing: border-box; }
  html, body { width: 1200px; height: 848px; overflow: hidden; }
  body {
    background: var(--page-bg);
    font-family: "Lato", sans-serif;
    position: relative;
  }
  .card {
    position: absolute;
    left: 263px;
    width: 674px;
    height: 380px;
    box-shadow: 0 4px 14px rgba(0,0,0,0.18);
    overflow: hidden;
  }
  .card--front { top: 28px; background: var(--card-white); }
  .card--back { top: 440px; background: var(--brand-blue); color: var(--card-white); }

  /* Brand lockup */
  .brand-mark {
    position: absolute;
    display: flex;
    align-items: center;
    gap: 10px;
    white-space: nowrap;
    font-weight: 700;
  }
  .brand-mark__dot { flex: none; border-radius: 50%; }

  .brand-mark--small {
    right: 38px;
    top: 132px;
    color: var(--brand-blue);
    font-size: 22px;
    letter-spacing: 0.5px;
  }
  .brand-mark--small .brand-mark__dot { width: 12px; height: 12px; background: var(--brand-green); }

  .brand-mark--large {
    left: 0; right: 0;
    top: 108px;
    justify-content: center;
    color: var(--card-white);
    font-size: 31px;
    letter-spacing: 2px;
  }
  .brand-mark--large .brand-mark__dot { width: 18px; height: 18px; background: var(--card-white); }

  /* Front */
  .person { position: absolute; left: 37px; top: 152px; }
  .person__name { color: var(--brand-blue); font-weight: 700; font-size: 20px; line-height: 24px; }
  .person__role { color: var(--text-grey); font-size: 17px; line-height: 22px; }
  .address { position: absolute; left: 37px; top: 215px; color: var(--text-grey); font-size: 17px; line-height: 23px; }
  .contact { position: absolute; left: 37px; top: 278px; list-style: none; color: var(--text-grey); font-size: 17px; line-height: 23px; }
  .contact li { display: flex; align-items: center; gap: 9px; }
  .contact svg { width: 12px; height: 12px; fill: var(--brand-blue); flex: none; }

  /* Back */
  .services { position: absolute; left: 0; right: 0; top: 228px; text-align: center; }
  .services__title {
    display: inline-block;
    font-weight: 700;
    font-size: 25px;
    line-height: 30px;
    padding: 0 8px 4px;
    border-bottom: 2px solid var(--card-white);
  }
  .services__list { list-style: none; margin-top: 10px; font-size: 20px; line-height: 31px; }
  .services__row { display: flex; justify-content: center; gap: 14px; }
  .services__row span::before {
    content: "";
    display: inline-block;
    width: 11px; height: 11px;
    border-radius: 50%;
    background: var(--card-white);
    margin-right: 10px;
    vertical-align: 1px;
  }
</style>
</head>
<body>
  <section class="card card--front" aria-label="Vorderseite">
    <div class="brand-mark brand-mark--small">
      <span class="brand-mark__dot"></span>
      <span>Varomir Facility Services</span>
    </div>
    <div class="person">
      <p class="person__name">Tarik Kostelac</p>
      <p class="person__role">Geschäftsführer</p>
    </div>
    <p class="address">Birkenhaldweg 14<br>6330 Cham</p>
    <ul class="contact">
      <li><svg viewBox="0 0 24 24"><path d="M6.6 10.8a15.1 15.1 0 0 0 6.6 6.6l2.2-2.2a1 1 0 0 1 1-.25 11.4 11.4 0 0 0 3.6.57 1 1 0 0 1 1 1V20a1 1 0 0 1-1 1A17 17 0 0 1 3 4a1 1 0 0 1 1-1h3.5a1 1 0 0 1 1 1c0 1.25.2 2.45.57 3.57a1 1 0 0 1-.25 1z"/></svg>+41 76 519 47 83</li>
      <li><svg viewBox="0 0 24 24"><path d="M2 5h20v14H2z M2 5l10 8 10-8" fill="none" stroke="#246BB0" stroke-width="2.4"/><path d="M2 5h20l-10 8z"/></svg>info@varomir-fs.ch</li>
      <li><svg viewBox="0 0 24 24"><circle cx="12" cy="12" r="9.5" fill="none" stroke="#246BB0" stroke-width="2"/><ellipse cx="12" cy="12" rx="4" ry="9.5" fill="none" stroke="#246BB0" stroke-width="2"/><path d="M2.5 12h19M4 7h16M4 17h16" stroke="#246BB0" stroke-width="1.8"/></svg>www.varomir-fs.ch</li>
    </ul>
  </section>

  <section class="card card--back" aria-label="Rückseite">
    <div class="brand-mark brand-mark--large">
      <span class="brand-mark__dot"></span>
      <span>VAROMIR FACILITY SERVICES</span>
    </div>
    <div class="services">
      <h2 class="services__title">Services</h2>
      <ul class="services__list">
        <li class="services__row"><span>Maintenance cleaning</span><span>Industrial cleaning</span></li>
        <li class="services__row"><span>Cleaning</span><span>Caretaking</span><span>Gardening, disposal</span></li>
      </ul>
    </div>
  </section>
</body>
</html>
```